So the ones in the picture are my original cards that I came up with. 😅however I kinda messed up on two things, I missed spelled my name it should be Marcello Vandora as well as the email should be Marcellov@brightlanecrews.com. I would like to clean this card up and also make it pop! Something that people would remember me by and that screams DEMOLITION. As well as a card that give you a feeling of loyalty and trust. I would also like to change and remove junk hauling and add full demolition to replace it. These cards worked for a little while but I cant make that my image while handing these out. I would also like to only put down that we are located in Lakemont Springs, CA, 90417 instead of the address on the card. Also if we can have a line that states Licensed, Bonded, & Insured. With out License # 4837215

Target Market(s)

Contractors and Home owners

Industry/Entity Type

Construction specialist in Demolition

Contact Information for Business Card

R Wrecking Selective Demolition & Full Demolition Kitchens AD Preparation Bathrooms Sheds Interiors & Exteriors Demo Digging And Much More Marcello Vandora Owner our city state and zip

Font styles to use
Serif
Sans Serif
Decorative

Colors
0054AA
0677BA
7BADD7
CADEEF
E8F1F8
0094D4
00A9DD
6FCCEA
C7EBF8
E9F6FB

Requirements
Must have
• License# 4837215
Nice to have
• Trying to go with a blue and white color scheme
Should not have
• Building construction

```html
<!DOCTYPE html>
<html lang="en">
<head>
<meta charset="UTF-8">
<title>R Wrecking — Business Card</title>
<link rel="stylesheet" href="https://fonts.googleapis.com/css2?family=Oswald:wght@600&family=Open+Sans:wght@700&family=Noto+Serif:wght@400;700&display=swap">
<style>
  :root {
    --stage: #2b2b2d;
    --card-white: #ffffff;
    --brand-blue: #0054aa;
    --card-blue: #0f4f9a;
    --ink: #111111;
    --on-blue: #ffffff;
    --rule: rgba(255,255,255,0.75);
  }
  * { margin: 0; padding: 0; box-sizing: border-box; }
  html, body { width: 1200px; height: 875px; overflow: hidden; }
  body {
    background: var(--stage);
    position: relative;
    font-family: "Noto Serif", serif;
  }
  .card {
    position: absolute;
    width: 560px;
    height: 320px;
    border-radius: 22px;
    overflow: hidden;
  }

  /* Front */
  .card--front {
    left: 50px; top: 110px;
    background: var(--card-white);
  }
  .front-lockup {
    position: absolute;
    left: 80px; top: 108px;
    display: flex; align-items: center; gap: 18px;
  }
  .front-mark {
    width: 62px; height: 62px;
    background: var(--brand-blue);
    border-radius: 10px;
  }
  .front-name {
    font-family: "Oswald", sans-serif;
    font-weight: 600;
    font-size: 64px;
    line-height: 1;
    letter-spacing: 1px;
    color: var(--brand-blue);
    text-transform: uppercase;
  }
  .front-license {
    position: absolute;
    left: 240px; top: 196px;
    font-family: "Open Sans", sans-serif;
    font-weight: 700;
    font-size: 20px;
    letter-spacing: 1px;
    color: var(--ink);
  }

  /* Back */
  .card--back {
    left: 590px; top: 445px;
    background: var(--card-blue);
    color: var(--on-blue);
  }
  .back-brand {
    position: absolute;
    left: 34px; top: 70px;
    width: 150px;
    display: flex; flex-direction: column; align-items: center; gap: 12px;
  }
  .back-mark {
    width: 78px; height: 78px;
    background: var(--on-blue);
    border-radius: 14px;
  }
  .back-brand-name {
    font-family: "Noto Serif", serif;
    font-weight: 700;
    font-size: 20px;
    letter-spacing: 1px;
    text-transform: uppercase;
    color: var(--on-blue);
  }
  .back-divider {
    position: absolute;
    left: 205px; top: 40px;
    width: 1px; height: 150px;
    background: var(--rule);
  }
  .back-contact {
    position: absolute;
    left: 228px; top: 34px;
  }
  .owner-name {
    font-weight: 700;
    font-size: 22px;
    letter-spacing: 1px;
    text-transform: uppercase;
    line-height: 1.1;
  }
  .owner-title { font-size: 14px; margin-bottom: 10px; }
  .contact-list { list-style: none; font-size: 12.5px; line-height: 1.65; }
  .contact-list li { display: flex; align-items: center; gap: 8px; }
  .contact-list svg { width: 12px; height: 12px; flex: none; }
  .credentials {
    margin-top: 10px;
    font-weight: 700;
    font-size: 13px;
    letter-spacing: 0.5px;
    text-transform: uppercase;
  }
  .services {
    position: absolute;
    left: 34px; right: 24px; top: 218px;
    font-size: 13px;
    line-height: 1.55;
  }
  .services-title {
    font-weight: 700;
    text-transform: uppercase;
    letter-spacing: 0.4px;
  }
</style>
</head>
<body>

  <section class="card card--front" aria-label="Business card front">
    <div class="front-lockup">
      <span class="front-mark" aria-hidden="true"></span>
      <span class="front-name">R Wrecking</span>
    </div>
    <p class="front-license">LICENSE# 4837215</p>
  </section>

  <section class="card card--back" aria-label="Business card back">
    <div class="back-brand">
      <span class="back-mark" aria-hidden="true"></span>
      <span class="back-brand-name">R Wrecking</span>
    </div>

    <div class="back-divider" aria-hidden="true"></div>

    <div class="back-contact">
      <h1 class="owner-name">Marcello Vandora</h1>
      <p class="owner-title">Owner</p>
      <ul class="contact-list">
        <li>
          <svg viewBox="0 0 24 24" aria-hidden="true"><path fill="#fff" d="M6.6 10.8a15.1 15.1 0 0 0 6.6 6.6l2.2-2.2c.3-.3.7-.4 1-.2 1.1.4 2.3.6 3.6.6.6 0 1 .4 1 1V20c0 .6-.4 1-1 1A17 17 0 0 1 3 4c0-.6.4-1 1-1h3.5c.6 0 1 .4 1 1 0 1.3.2 2.5.6 3.6.1.3 0 .7-.2 1z"/></svg>
          (555) 318-2740
        </li>
        <li>
          <svg viewBox="0 0 24 24" aria-hidden="true"><path fill="#fff" d="M2 5h20v14H2z M2 5l10 8 10-8" stroke="#0f4f9a" stroke-width="1.5"/></svg>
          Marcellov@brightlanecrews.com
        </li>
        <li>
          <svg viewBox="0 0 24 24" aria-hidden="true"><path fill="#fff" d="M12 2a7 7 0 0 0-7 7c0 5 7 13 7 13s7-8 7-13a7 7 0 0 0-7-7zm0 9.5A2.5 2.5 0 1 1 12 6.5a2.5 2.5 0 0 1 0 5z"/></svg>
          Lakemont Springs, CA, 90417
        </li>
      </ul>
      <p class="credentials">Licensed, Bonded, &amp; Insured</p>
    </div>

    <div class="services">
      <p class="services-title">R Wrecking Selective Demolition &amp; Full Demolition</p>
      <p>Kitchens • ADU Preparation • Bathrooms • Sheds</p>
      <p>Interiors and Exteriors Demo • Digging and Much More</p>
    </div>
  </section>

</body>
</html>
```